Fabrication and machining company needing printed material designs.

Heron Vessels, Inc. wants to use appealing visuals as well as informative text to tell potential clients about our capabilities in fabrication and machining. We have a new logo to showcase as well as a new website. The use of print media will allow us to leave tangible information with clients, and therefore the design will need to be concise, informative, and visually appealing.

Full Page Flyer (approx. 8.5" x 11"), front and back design. This will be a detailed offering of capabilities and services for our shop.

Half Page Flyer (approx. 5.5" x 8.5"), front and back design. An abbreviated version of the full page flyer, meant to be easily handed out and stored inside a note book.

Bi-fold business card front and back. General offerings of our services. Minimal if any details. Finished size is twice the size of a business card (approx. 4" x 3.5"), once folded in half will be the same size as a standard business card (approx. 2" x 3.5").

Please use www.heronvesselsinc.example for theme ideas. The font used for our logo is ethnocentric, not to be used for all text.

Target Market(s)

Industrial Consumers

Font styles to use
Sans Serif

```html
<!DOCTYPE html>
<html lang="en">
<head>
<meta charset="utf-8">
<title>Heron Vessels, Inc. — Fabrication and Machining Flyer</title>
<link rel="stylesheet" href="https://fonts.googleapis.com/css2?family=Orbitron:wght@700;900&family=Archivo:wght@400;600;700;800&display=swap">
<style>
  :root{
    --stage:#c9c9c9;
    --paper:#ffffff;
    --orange:#e2761b;
    --charcoal:#3b3b3d;
    --ink:#2a2a2a;
    --muted:#555555;
    --display:'Orbitron', sans-serif;
    --text:'Archivo', sans-serif;
  }
  *{box-sizing:border-box;margin:0;padding:0}
  html,body{width:1200px;height:960px;overflow:hidden;background:var(--stage);font-family:var(--text)}
  ul{list-style:none}
  .sheet{position:absolute;top:130px;width:540px;height:700px;background:var(--paper);overflow:hidden;box-shadow:0 6px 18px rgba(0,0,0,.18)}
  .sheet--front{left:40px}
  .sheet--back{left:620px}

  /* Front */
  .front-photo{position:absolute;left:22px;top:22px;right:22px;bottom:22px;
    background:linear-gradient(180deg,#4e97db 0%,#8cc0ea 28%,#c7ccd2 45%,#8e9399 70%,#5d6268 100%)}
  .front-band{position:absolute;left:22px;right:0;top:80px;height:130px;background:var(--orange);display:flex;align-items:center;padding:0 22px}
  .brand{display:flex;flex-direction:column;align-items:flex-start;gap:8px;width:170px}
  .brand__mark{width:44px;height:44px;background:#fff}
  .brand__name{font-weight:700;font-size:13px;color:#fff;letter-spacing:.02em}
  .front-title{margin-left:12px}
  .front-title h1{font-family:var(--display);font-weight:900;color:#fff;font-size:25px;line-height:1.1;letter-spacing:.02em}
  .front-title p{color:#fff;font-weight:700;font-size:11.5px;margin-top:10px}

  /* Back: dark capabilities area */
  .back-dark{position:absolute;left:0;top:0;width:540px;height:340px;background:var(--charcoal)}
  .back-title{position:absolute;left:26px;top:22px;font-family:var(--display);font-weight:900;font-size:36px;color:#fff;letter-spacing:.04em}
  .cap{position:absolute;color:#fff}
  .cap h3{color:var(--orange);font-size:12.5px;font-weight:700;line-height:1.15}
  .cap li{font-size:10.5px;line-height:1.35;color:#e8e8e8}
  .cap li::before{content:"› "}
  .cap-block{margin-bottom:8px}
  .cap-lead{font-size:16px;font-weight:800;color:#fff;line-height:1.1;margin-bottom:8px}
  .cap--left{left:26px;top:80px;width:175px}
  .cap--right{left:210px;top:80px;width:155px}

  .photo{position:absolute}
  .photo--lathe{left:370px;top:70px;width:170px;height:270px;background:linear-gradient(160deg,#2a2622 0%,#6b5a4a 40%,#d37a2c 70%,#3c342e 100%)}
  .photo--pump{left:0;top:240px;width:205px;height:100px;background:linear-gradient(135deg,#6f6a64 0%,#b42a22 45%,#d9413a 60%,#5f5a55 100%)}
  .photo--welder{left:375px;top:450px;width:165px;height:204px;background:linear-gradient(135deg,#2b3646 0%,#3f5a7a 50%,#e8a25a 80%,#2d2a28 100%)}

  /* Specialities panel */
  .specials{position:absolute;left:205px;top:340px;width:335px;height:110px;background:var(--orange);color:#fff;padding:10px 18px}
  .specials h2{font-size:19px;font-weight:800;line-height:1.2;margin-bottom:4px}
  .specials__cols{display:flex;gap:30px}
  .specials li{font-size:10.5px;line-height:1.4}
  .specials li::before{content:"› "}

  /* White service lists */
  .service{position:absolute;color:var(--ink)}
  .service h3{color:var(--orange);font-size:11.5px;font-weight:700;line-height:1.15}
  .service li{font-size:9.5px;line-height:1.3;color:var(--muted)}
  .service li::before{content:"› "}
  .service-block{margin-bottom:6px}
  .service--b .service-block{margin-bottom:4px}
  .service--a{left:20px;top:356px;width:185px}
  .service--b{left:214px;top:460px;width:155px}

  /* Footer */
  .footer{position:absolute;left:200px;top:654px;width:340px;height:46px;background:var(--charcoal);display:flex;align-items:center;padding:0 14px;gap:12px}
  .footer__brand{display:flex;align-items:center;gap:6px;width:118px}
  .footer__mark{width:16px;height:16px;background:var(--orange);flex:none}
  .footer__name{color:var(--orange);font-weight:700;font-size:11px;line-height:1.1}
  .footer__contact{color:#fff;line-height:1.15}
  .footer__addr{font-size:9px}
  .footer__web{font-size:10.5px;font-weight:700}
  .footer__phone{display:flex;align-items:center;gap:5px;font-size:15px;font-weight:800}
</style>
</head>
<body>

<section class="sheet sheet--front" aria-label="Flyer front">
  <div class="front-photo" role="img" aria-label="Row of tall stainless steel storage tanks against a blue sky"></div>
  <div class="front-band">
    <div class="brand">
      <div class="brand__mark"></div>
      <span class="brand__name">Heron Vessels, Inc.</span>
    </div>
    <div class="front-title">
      <h1>FABRICATION<br>AND MACHINING</h1>
      <p>ISO 9001 API TANKS 12F, 620, 650 AWWA</p>
    </div>
  </div>
</section>

<section class="sheet sheet--back" aria-label="Flyer back">
  <div class="back-dark"></div>
  <h2 class="back-title">CAPABILITIES</h2>

  <div class="cap cap--left">
    <div class="cap-block"><h3>Horizontal Lathes</h3><ul><li>Up To 24" Dia &amp; 10' Long</li></ul></div>
    <div class="cap-lead">Horizontal Boring<br>Mill Capabilities</div>
    <div class="cap-block"><h3>CNC Plasma Cutting</h3><ul><li>8X20 Capacity</li></ul></div>
    <div class="cap-block"><h3>Band Saws</h3><ul><li>22 Cut Capacity</li></ul></div>
  </div>

  <div class="cap cap--right">
    <div class="cap-block"><h3>Vertical Lathes</h3><ul><li>Up To 44" Dia</li></ul></div>
    <div class="cap-block"><h3>Press Brake</h3><ul><li>1 Plate 5 Wide</li><li>38 Plate x 1 Wide</li></ul></div>
    <div class="cap-block"><h3>CNC Roll Forming</h3><ul><li>1/2 X 10 Capacity</li></ul></div>
    <div class="cap-block"><h3>Iron Workers</h3><ul><li>Up To 85 Tons</li></ul></div>
  </div>

  <div class="photo photo--lathe" role="img" aria-label="Lathe cutting a steel shaft with sparks"></div>
  <div class="photo photo--pump" role="img" aria-label="Red pump skid on gravel"></div>

  <div class="specials">
    <h2>Specialities</h2>
    <div class="specials__cols">
      <ul><li>Walkways &amp; Stairs</li><li>Fire Tubes</li><li>Pump Skids</li><li>Tank Vents</li></ul>
      <ul><li>Trailer Components</li><li>Tanks</li><li>Clarifiers</li><li>Piping</li></ul>
    </div>
  </div>

  <div class="service service--a">
    <div class="service-block"><h3>Insulating systems</h3><ul><li>Polyurethane Spray Foam</li><li>Metal Wrap</li><li>Heat Trace</li></ul></div>
    <div class="service-block"><h3>Welding Processes</h3><ul><li>Carbon Steel</li><li>Stainless Steel</li></ul></div>
    <div class="service-block"><h3>Corrosion Control</h3><ul><li>Paint Bay</li><li>Spray Liner Systems</li><li>Stainless Steel Passivation</li><li>Plural Component Application Equip</li><li>Powder Coating</li><li>Galvanizing</li></ul></div>
    <div class="service-block"><h3>Facility</h3><ul><li>35,000 ft Facility</li><li>5 Acre Storage Yard</li></ul></div>
  </div>

  <div class="service service--b">
    <div class="service-block"><h3>Design and Engineering</h3><ul><li>CAD Drawings</li><li>Engineering Services</li><li>3D Modeling</li></ul></div>
    <div class="service-block"><h3>Hydraulic Assemblies</h3><ul><li>System Testing</li><li>Hose Assemblies</li><li>Ram Rebuilding</li></ul></div>
    <div class="service-block"><h3>Drivelines</h3><ul><li>Custom built</li><li>Rebuilding</li><li>Straightening</li></ul></div>
    <div class="service-block"><h3>Sandblasting</h3><ul><li>High Production Capacity</li></ul></div>
  </div>

  <div class="photo photo--welder" role="img" aria-label="Worker in hard hat grinding metal with sparks"></div>

  <footer class="footer">
    <div class="footer__brand">
      <div class="footer__mark"></div>
      <span class="footer__name">Heron Vessels, Inc.</span>
    </div>
    <div class="footer__contact">
      <div class="footer__addr">1460 North Ridge Rd Alder, UT 84900</div>
      <div class="footer__web">www.heronvesselsinc.example</div>
      <div class="footer__phone">
        <svg width="13" height="13" viewBox="0 0 24 24" aria-hidden="true"><path fill="#fff" d="M6.6 10.8a15.1 15.1 0 0 0 6.6 6.6l2.2-2.2c.3-.3.7-.4 1-.2 1.1.4 2.3.6 3.6.6.6 0 1 .4 1 1V20c0 .6-.4 1-1 1A17 17 0 0 1 3 4c0-.6.4-1 1-1h3.5c.6 0 1 .4 1 1 0 1.3.2 2.5.6 3.6.1.3 0 .7-.2 1z"/></svg>
        555-014-2290
      </div>
    </div>
  </footer>
</section>

</body>
</html>
```